KorvaNest - Home Income and Business Resources Platform

I am looking for a website template for a multi-purposed website. This website will feature:

1.) Website Directory with Ratings & comments on listings
2.) Company Blog
3.) Homepage with Content (see files for homepage mock)

I would like the Design to have a default width 1170px (wider then normal)

Of course I am looking for Pages for Listings to be designed.

Great looking BLOG Layout: http://journal.plimworks.example/html/blog.html

I would like 4 Versions of a Website Directory Listing "Box"
1.) Basic Listing Box
2.) Sponsored Listing Box
3.) Recommended Listing Box
4.) Stay Away From Listing Box

Information on the Listing Page (Like on a Category Page)
Site Name, Site URL, Website Image, # of Views, Rating and # of Comments

Information on the Listing Details Page:
Same as ABOVE + About website Description, Vornic Score, Category Information

Decent looking examples is here: https://samples.trevolin.example/directory/computers/ and http://www.zqrankhub.example/.

I will include some sketches and screenshots of things I like/looking for. As designers,you have creative freedom and are encouraged to show this. This is Phase one of this project and winning designer is guaranteed to have future work for this project.

Target Market(s)

Directory, business, websites

Industry/Entity Type

Business

Coding

Coded - Design and coding required

Number of Pages Required

5+ page

Font styles to use
Sans Serif

Colors

Designer to choose colors to be used in the design.

Requirements
Must have
• Professional yet clean look. The use of Icons & images
• Unique Look
Should not have
• Any exact copies of any examples I provided

```html
<!DOCTYPE html>
<html lang="en">
<head>
<meta charset="utf-8">
<title>KorvaNest – Home</title>
<link rel="stylesheet" href="https://fonts.googleapis.com/css2?family=Open+Sans:wght@400;600;700&family=Raleway:wght@400;500&display=swap">
<style>
:root{
  --brand:#2f6f9c;
  --brand-dark:#2a5f86;
  --ink:#1d1d1d;
  --link:#1f7bc1;
  --teal:#46b39b;
  --yellow:#efc94c;
  --orange:#e67a3f;
  --panel:#ffffff;
  --sky-top:#dfe9f1;
  --sky-bottom:#cfdbe5;
  --ad-green:#1f8c22;
  --ad-orange:#f0a000;
}
*{box-sizing:border-box;margin:0;padding:0}
html,body{width:1200px;height:928px;overflow:hidden}
body{
  position:relative;
  font-family:"Open Sans",sans-serif;
  background:linear-gradient(180deg,var(--sky-top) 0%,#e6edf2 55%,var(--sky-bottom) 100%);
  color:var(--ink);
}
.cloud{position:absolute;background:#f2f5f8;border-radius:50%;opacity:.8}
/* header */
.site-header{position:absolute;left:0;top:0;width:1200px;height:83px}
.brand{position:absolute;left:60px;top:18px;font-size:37px;font-weight:600;color:var(--brand);letter-spacing:1px}
.main-nav{position:absolute;left:353px;top:34px;display:flex;gap:31px}
.main-nav a{font-family:"Raleway",sans-serif;font-weight:500;font-size:12.5px;color:#222;text-decoration:none;letter-spacing:.2px}
.main-nav a.active{color:var(--brand)}
.btn-login{position:absolute;left:1045px;top:24px;width:96px;height:36px;border-radius:8px;background:var(--brand);color:#fff;font-family:"Raleway",sans-serif;font-weight:500;font-size:13px;display:flex;align-items:center;justify-content:center}
/* panel */
.content-panel{position:absolute;left:60px;top:83px;width:1081px;height:807px;background:var(--panel);border-radius:10px;box-shadow:0 0 4px rgba(0,0,0,.12)}
/* about */
.about-card{position:absolute;left:15px;top:19px;width:782px;height:213px;border-radius:10px;background:#fff;box-shadow:0 1px 4px rgba(0,0,0,.18);overflow:hidden}
.about-photo{position:absolute;left:0;top:0;width:330px;height:213px;background:linear-gradient(135deg,#c9cfc0,#9aa79a 50%,#5d7a88);clip-path:polygon(0 0,100% 0,83% 100%,0 100%)}
.about-text{position:absolute;left:343px;top:37px;width:420px}
.about-text h2{font-size:16px;font-weight:600;color:var(--brand);letter-spacing:1px;margin-bottom:13px}
.about-text p{font-size:14px;line-height:23px;color:#666}
/* feature cards */
.feature-card{position:absolute;top:250px;width:250px;height:430px;border-radius:10px;overflow:hidden;box-shadow:0 3px 3px rgba(0,0,0,.15)}
.feature-card .photo{height:184px}
.feature-card .body{height:246px;padding:22px 14px 0 20px;color:#fff}
.feature-card .title{display:flex;align-items:center;gap:8px;padding-bottom:18px;border-bottom:1px solid rgba(255,255,255,.3);margin-right:4px}
.feature-card .title svg{flex:none}
.feature-card h3{font-size:13.5px;font-weight:700;letter-spacing:.5px;line-height:18.5px;white-space:nowrap}
.feature-card p{font-size:13px;line-height:23px;margin-top:14px}
.feature-card .more{display:block;margin-top:18px;font-size:13px;font-weight:700;letter-spacing:.8px}
.card-home{left:15px}.card-home .body{background:var(--teal)}
.card-home .photo{background:linear-gradient(135deg,#3d3f45,#c7a86a 55%,#8a6a4a)}
.card-ads{left:281px}.card-ads .body{background:var(--yellow)}
.card-ads .body p,.card-ads .body .more{color:#fff8e0}
.card-ads .photo{background:linear-gradient(135deg,#2c2c2c,#bfc3c7 50%,#eceeef)}
.card-earn{left:546px}.card-earn .body{background:var(--orange)}
.card-earn .photo{background:linear-gradient(135deg,#7a9a3a,#c9a060 50%,#6d7a3a)}
/* sponsored */
.sponsored{position:absolute;left:825px;top:19px;width:240px;height:413px;border-radius:10px;background:#fff;box-shadow:0 1px 4px rgba(0,0,0,.18);padding:20px 19px 0 19px}
.sponsored h2{font-size:16.5px;font-weight:700;letter-spacing:.8px;margin-left:3px;margin-bottom:10px}
.listing{display:flex;align-items:center;height:92px;border-bottom:1px solid #e2e2e2}
.listing:last-child{border-bottom:none}
.listing .name{width:106px;flex:none;font-weight:700;font-size:17px;color:var(--brand-dark)}
.listing a{font-family:"Raleway",sans-serif;font-weight:500;font-size:14.5px;line-height:19px;color:var(--link);text-decoration:none}
/* ad */
.survey-ad{position:absolute;left:829px;top:449px;width:230px;height:229px;background:linear-gradient(110deg,var(--ad-green) 0%,var(--ad-green) 48%,var(--ad-orange) 52%,#d9b899 62%,#eceeee 100%)}
/* footer */
.copyright{position:absolute;left:0;width:1081px;top:715px;text-align:center;font-family:"Raleway",sans-serif;font-size:12.5px;color:var(--brand)}
.social{position:absolute;left:413px;top:750px;display:flex;gap:24px}
.social span{width:17px;height:17px;border-radius:50%;background:var(--brand)}
</style>
</head>
<body>
<div class="cloud" style="left:-60px;top:640px;width:340px;height:260px"></div>
<div class="cloud" style="left:1080px;top:260px;width:200px;height:160px"></div>
<div class="cloud" style="left:1010px;top:720px;width:260px;height:220px"></div>
<div class="cloud" style="left:380px;top:850px;width:460px;height:200px"></div>

<header class="site-header">
  <div class="brand">KORVANEST</div>
  <nav class="main-nav">
    <a class="active" href="#">HOME</a>
    <a href="#">ABOUT US</a>
    <a href="#">RESOURCES</a>
    <a href="#">BENEFITS</a>
    <a href="#">EARNING</a>
    <a href="#">SPONSORS</a>
    <a href="#">CONTACT US</a>
  </nav>
  <div class="btn-login">LOG IN</div>
</header>

<main class="content-panel">
  <section class="about-card">
    <div class="about-photo" role="img" aria-label="Couple on a sofa reviewing papers together"></div>
    <div class="about-text">
      <h2>ABOUT KORVANEST</h2>
      <p>Aliquam molestie, mi et imperdiet euismod, dui purus auctor tellus, et interdum lacus lectus et anteaccumsan sollicitudin sapien, sit amet adipiscing turpis gravida ac aliquam nibh a dui iaculis viverra id a velit. Vivamus egestas risus in magna varius commodo.</p>
    </div>
  </section>

  <article class="feature-card card-home">
    <div class="photo" role="img" aria-label="Person signing papers beside a small model house"></div>
    <div class="body">
      <div class="title">
        <svg width="32" height="40" viewBox="0 0 35 40" aria-hidden="true"><path d="M2 1h22l9 9v29H2z" fill="#fff"/><path d="M24 1v9h9" fill="none" stroke="#46b39b" stroke-width="2"/><rect x="9" y="18" width="17" height="2.5" fill="#46b39b"/><rect x="9" y="24" width="17" height="2.5" fill="#46b39b"/><rect x="9" y="30" width="17" height="2.5" fill="#46b39b"/></svg>
        <h3>HOME INCOME<br>RESOURCE DIRECTORY</h3>
      </div>
      <p>Find what you need, when you need it.The KorvaNest website directory is your one-stop pit for anything involved...</p>
      <span class="more">LEARN MORE</span>
    </div>
  </article>

  <article class="feature-card card-ads">
    <div class="photo" role="img" aria-label="Businessman holding a tablet with advertising sketches"></div>
    <div class="body">
      <div class="title">
        <svg width="52" height="34" viewBox="0 0 52 34" aria-hidden="true"><rect x="8" y="3" width="36" height="23" rx="2" fill="none" stroke="#fff" stroke-width="3"/><path d="M1 29h50v2a2 2 0 0 1-2 2H3a2 2 0 0 1-2-2z" fill="#fff"/></svg>
        <h3>ADVERTISING<br>BENEFITS</h3>
      </div>
      <p>Everyone needs to advertise and we know just how to get your offer out to the right people. We have many methods...</p>
      <span class="more">LEARN MORE</span>
    </div>
  </article>

  <article class="feature-card card-earn">
    <div class="photo" role="img" aria-label="Hand planting seedlings on stacks of coins beside a clock"></div>
    <div class="body">
      <div class="title">
        <svg width="30" height="44" viewBox="0 0 30 44" aria-hidden="true"><text x="15" y="38" text-anchor="middle" font-family="Open Sans,sans-serif" font-weight="700" font-size="44" fill="#fff">$</text></svg>
        <h3>EARNING WITH<br>KORVANEST</h3>
      </div>
      <p>Join KorvaNest and start earning money. When you share KorvaNest and lock in an advertiser or premium listing,</p>
      <span class="more">LEARN MORE</span>
    </div>
  </article>

  <aside class="sponsored">
    <h2>SPONSORED LISTING</h2>
    <div class="listing"><span class="name">Ravelo</span><a href="#">Lorem ipsum<br>dolor sit..</a></div>
    <div class="listing"><span class="name">Brennick</span><a href="#">Lorem ipsum<br>dolor sit..</a></div>
    <div class="listing"><span class="name">Kemtor</span><a href="#">Lorem ipsum<br>dolor sit..</a></div>
    <div class="listing"><span class="name">Barlo</span><a href="#">Lorem ipsum<br>dolor sit..</a></div>
  </aside>

  <aside class="survey-ad" role="img" aria-label="Advertising banner: take surveys and get paid, start now, with a smiling woman at a laptop and the advertiser address www.ledgerpine.example"></aside>

  <p class="copyright">Copyrigit © 2017. Company Name. All Right Reserved</p>
  <div class="social" aria-label="Social links">
    <span></span><span></span><span></span><span></span><span></span><span></span>
  </div>
</main>
</body>
</html>
```